Silver Kite Venture Series Travel Brochure

I'm looking for a brochure design for a new travel product - Silver Kite Venture Series, catering for students above 12 years old. Target audience are schools that do destination projects. Brochure to be read by head teacher, parents and students.

Brochure should be A4 in size, 4-6 pages. Format of brochure is hard cover (a folder) with inlet for flyers. Flyers for destinations will be updated from time to time.

Finished job needs to be converted to electronic format for website and email proposal usage.

Attached is text to be used on brochure. Order of section can be adjusted.

For "Elements of the trip", please understand the contents and explain/display it in a graphic form.

For flyer, please come out with a template that I can use for other destinations. The main elements - what's included, number of days, location for pictures, itinerary, educational focus, should be alterable. Attached are text for two sample destinations.
Also attached (tour itinerary example) a version of flyer that I like.

I'm attaching some pictures here. If you find more suitable pictures, please feel free to use them.

Reason: I'm extending the deadline of this project by 4 days, as I need to add details & photo of another travel specialist in personnel session (total of 3 members). Also, in view of the amount of work a designer has to do for this project, I'm giving you more time for submission. Please do not hesitate to be in touch should you need more than 4 days extension. Thank you.

Target Market(s)

Schools - especially the head teacher and parents, to send students above 12 years old to travel

Industry/Entity Type

Electronic

Requirements
Must have
• This is a travel brochure with education elements in it. Parents feel better when their children are travelling for a purpose and lead by responsible teachers/adults whom they can trust. So, the design has to emphasis that education elements and safety are our utmost priority.
Nice to have
• We specialise in environmental study. So, it is nice to have the environmental touch in the design.
Should not have
• Our target market segment is the Middle East, which can be quite sensitive to religion. I prefer not to have any religious related illustration on the design.

```html
<!DOCTYPE html>
<html lang="en">
<head>
<meta charset="utf-8">
<title>Silver Kite Venture Series – Folder and Destination Flyers</title>
<link rel="stylesheet" href="https://fonts.googleapis.com/css2?family=Alfa+Slab+One&family=Open+Sans:wght@300;400;600;700&display=swap">
<style>
  :root{
    --leaf:#8cc63f;
    --leaf-dark:#3f9b35;
    --forest:#1f6b2a;
    --navy:#1b4f8a;
    --sky:#5aa0d8;
    --pocket-text:#2c5f8f;
    --ink:#22313f;
    --paper:#ffffff;
    --backdrop:#e7e9e7;
    --slab:"Alfa Slab One", Georgia, serif;
    --sans:"Open Sans", Arial, sans-serif;
  }
  *{box-sizing:border-box;margin:0;padding:0}
  html,body{width:1200px;height:900px;overflow:hidden}
  body{background:var(--backdrop);font-family:var(--sans);color:var(--ink);position:relative}

  .flyer,.folder{position:absolute;top:188px;width:370px;height:523px;overflow:hidden;box-shadow:0 2px 10px rgba(0,0,0,.12)}
  .flyer{background:var(--paper)}
  .flyer--egypt{left:24px}
  .folder{left:415px;background:var(--leaf)}
  .flyer--greece{left:806px}

  /* flyer header */
  .flyer-head{position:absolute;top:0;left:0;right:0;height:44px;display:flex;align-items:center;justify-content:space-between;padding:0 14px}
  .series-title{font-weight:300;color:var(--navy);font-size:15px;letter-spacing:.2px}
  .flyer--egypt .series-title{margin-left:70px}
  .leaf-corner{position:absolute;top:0;left:0;width:78px;height:44px;background:linear-gradient(135deg,#b6dd6a,#5fae32);border-bottom-right-radius:44px 30px}
  .consultancy{display:flex;align-items:center;gap:5px;font-size:9px;font-weight:600;color:var(--navy)}
  .consultancy-mark{width:10px;height:10px;background:var(--navy)}

  /* itinerary */
  .itinerary{position:absolute;background:var(--leaf);padding:12px 14px;list-style:none}
  .flyer--egypt .itinerary{top:44px;left:0;right:0;height:184px;column-count:2;column-gap:14px}
  .flyer--greece .itinerary{top:44px;left:190px;right:0;height:260px}
  .itinerary li{break-inside:avoid;margin-bottom:6px;font-size:8px;line-height:1.3;color:var(--forest);font-weight:600}
  .day{display:block;font-family:var(--slab);font-size:10px;color:var(--paper);font-weight:400}

  /* photo areas */
  .photo{position:absolute;left:0;width:190px}
  .photo--pyramids{top:228px;height:295px;background:linear-gradient(170deg,#d9b98a 0%,#b0895a 45%,#6b4a2c 100%)}
  .photo--columns{top:44px;height:479px;background:linear-gradient(180deg,#3a7cc4 0%,#6aa6dc 40%,#d8cfbf 62%,#9d9384 80%,var(--navy) 100%)}
  .destination{position:absolute;left:14px;bottom:18px;writing-mode:vertical-rl;transform:rotate(180deg);color:var(--paper);font-family:var(--slab);line-height:1}
  .destination-number{display:block;font-size:13px;margin-left:6px}
  .destination-name{display:block;font-size:42px;letter-spacing:1px}

  /* included list */
  .included{position:absolute;right:0;width:180px;padding:10px 12px;background:var(--paper)}
  .flyer--egypt .included{top:228px;height:150px}
  .flyer--greece .included{top:304px;height:219px}
  .included-title{font-family:var(--slab);font-weight:400;font-size:11px;color:var(--leaf-dark);margin-bottom:6px}
  .included ul{list-style:none}
  .included li{display:flex;align-items:center;gap:7px;font-size:8.5px;margin-bottom:3px;line-height:1.2}
  .included svg{width:16px;height:14px;flex:none}

  /* focus panel */
  .focus{position:absolute;top:378px;right:0;width:180px;height:145px;background:var(--navy);padding:8px 12px;color:var(--paper)}
  .focus-title{font-family:var(--slab);font-weight:400;font-size:11px;color:var(--leaf);margin-top:2px}
  .focus p{font-size:8.5px;line-height:1.25}

  /* folder inside */
  .sheet{position:absolute;top:14px;left:14px;right:0;bottom:0;background:var(--paper)}
  .sheet-title{position:absolute;top:14px;left:18px;font-family:var(--slab);font-weight:400;font-size:15px;color:var(--leaf-dark)}
  .wheel{position:absolute;top:46px;left:0;width:356px;height:280px}
  .element{position:absolute;width:96px;font-size:7px;line-height:1.3;color:var(--ink)}
  .element-name{font-family:var(--slab);font-weight:400;font-size:10px;color:var(--leaf-dark);display:block;margin-bottom:2px}
  .element--director{top:60px;left:256px}
  .element--visa{top:196px;left:268px;width:86px}
  .element--meals{top:52px;left:12px}
  .element--ticket{top:206px;left:10px;width:78px}
  .pocket{position:absolute;left:40px;right:0;bottom:0;height:190px;background:var(--sky);padding:34px 22px;text-align:center;color:var(--pocket-text);font-size:10px;line-height:1.5}
  .pocket p+p{margin-top:8px}
</style>
</head>
<body>

<article class="flyer flyer--egypt">
  <div class="leaf-corner" role="img" aria-label="Close-up of a green leaf"></div>
  <header class="flyer-head"><span class="series-title">Silver Kite Venture Series</span></header>
  <ol class="itinerary">
    <li><span class="day">Day 1</span>Arrival at Cairo – Cairo city tour – Pyramid and Sphinx</li>
    <li><span class="day">Day 2</span>Cairo Museum &amp; Khan El Khalili Bazaar – Cairo to Aswan by flight or train</li>
    <li><span class="day">Day 3</span>Embark on Nile Cruise – Visit high dam, unfinished obelisk, Philae temple</li>
    <li><span class="day">Day 4</span>Nile Cruise: visit Temple of Kom Ombo and Edfu Temple</li>
    <li><span class="day">Day 5</span>Nile Cruise: visit Temple of Karnak and Temple of Luxor</li>
    <li><span class="day">Day 6</span>Disembark from Nile Cruise – visit Luxor – Colossi of Memnon, Valley of the Kings, Hatshepsut Temple</li>
    <li><span class="day">Day 7</span>Luxor to Cairo by train</li>
    <li><span class="day">Day 8</span>Departure</li>
  </ol>
  <div class="photo photo--pyramids" role="img" aria-label="Photograph of the pyramids of Giza in warm evening light">
    <h2 class="destination"><span class="destination-number">Destination 3</span><span class="destination-name">EGYPT</span></h2>
  </div>
  <section class="included">
    <h3 class="included-title">What's included in price:</h3>
    <ul>
      <li><svg viewBox="0 0 16 14"><rect x="0" y="3" width="16" height="8" fill="#22313f"/></svg>Air ticket</li>
      <li><svg viewBox="0 0 16 14"><rect x="1" y="6" width="14" height="4" fill="#3f9b35"/><rect x="1" y="3" width="4" height="3" fill="#3f9b35"/></svg>All accommodation</li>
      <li><svg viewBox="0 0 16 14"><circle cx="8" cy="3" r="2.5" fill="#22313f"/><rect x="5" y="6" width="6" height="8" fill="#22313f"/></svg>Full time tour director</li>
      <li><svg viewBox="0 0 16 14"><circle cx="8" cy="7" r="6" fill="#3f9b35"/></svg>Meals</li>
      <li><svg viewBox="0 0 16 14"><rect x="4" y="1" width="1.5" height="13" fill="#22313f"/><rect x="5.5" y="1" width="8" height="5" fill="#3f9b35"/></svg>Tours led by local expert tour guides</li>
      <li><svg viewBox="0 0 16 14"><rect x="1" y="3" width="14" height="8" fill="#3f9b35"/></svg>Entrance fees to attractions</li>
    </ul>
  </section>
  <section class="focus">
    <h3 class="focus-title">Main focus subject</h3>
    <p>History and Anthropology</p>
    <h3 class="focus-title">Related subjects</h3>
    <p>Geography<br>Development Studies<br>Agriculture<br>Environmental Management</p>
    <h3 class="focus-title">Environmental focus</h3>
    <p>Impact of climate change on the Nile river basin.</p>
  </section>
</article>

<section class="folder">
  <div class="sheet">
    <h2 class="sheet-title">What's in our trips?</h2>
    <svg class="wheel" viewBox="0 0 356 280" aria-hidden="true">
      <g stroke="#8cc63f" stroke-width="1" fill="#8cc63f">
        <line x1="232" y1="72" x2="262" y2="30"/><circle cx="262" cy="30" r="3"/>
        <line x1="262" y1="150" x2="300" y2="152"/><circle cx="300" cy="152" r="3"/>
        <line x1="112" y1="72" x2="86" y2="34"/><circle cx="86" cy="34" r="3"/>
        <line x1="80" y1="170" x2="50" y2="180"/><circle cx="50" cy="180" r="3"/>
      </g>
      <circle cx="172" cy="140" r="92" fill="#3f9b35"/>
      <circle cx="172" cy="140" r="52" fill="#8cc63f" stroke="#b6dd6a" stroke-width="3"/>
      <g fill="#ffffff">
        <rect x="118" y="66" width="24" height="20" rx="3"/>
        <rect x="200" y="66" width="24" height="20" rx="3"/>
        <rect x="230" y="126" width="30" height="18" rx="3"/>
        <rect x="212" y="196" width="24" height="16" rx="3"/>
        <rect x="86" y="162" width="30" height="16" rx="3"/>
        <rect x="96" y="110" width="20" height="16" rx="3"/>
        <rect x="160" y="52" width="24" height="16" rx="3"/>
      </g>
      <g fill="#1f6b2a">
        <circle cx="130" cy="76" r="4"/>
        <circle cx="212" cy="73" r="3"/><rect x="209" y="77" width="6" height="7"/>
        <rect x="234" y="130" width="8" height="10"/>
        <rect x="215" y="200" width="14" height="8"/>
        <rect x="90" y="166" width="22" height="8"/>
        <rect x="99" y="116" width="14" height="5"/>
        <rect x="166" y="56" width="12" height="8"/>
      </g>
      <text x="172" y="128" text-anchor="middle" font-family="'Alfa Slab One', Georgia, serif" font-size="12" fill="#ffffff">WHAT'S</text>
      <text x="172" y="142" text-anchor="middle" font-family="'Alfa Slab One', Georgia, serif" font-size="12" fill="#ffffff">INCLUDED</text>
      <text x="172" y="156" text-anchor="middle" font-family="'Alfa Slab One', Georgia, serif" font-size="12" fill="#ffffff">IN THE</text>
      <text x="172" y="170" text-anchor="middle" font-family="'Alfa Slab One', Georgia, serif" font-size="12" fill="#ffffff">COST?</text>
    </svg>
    <p class="element element--director"><span class="element-name">Full time tour director</span>This person is your guide, friend and support throughout the trip. We will have at least one tour director with the group from the start and throughout the journey. Ratio is 1:8, one director or teacher to eight students.</p>
    <p class="element element--visa"><span class="element-name">Visa</span>We will assist with entry visas for all of the participants.</p>
    <p class="element element--meals"><span class="element-name">Meals</span>Meals for the students are planned at each stop, with local dishes included.</p>
    <p class="element element--ticket"><span class="element-name">Air ticket</span>We search for the best flight options available to you.</p>
    <div class="pocket">
      <p>Above are some of our more popular destinations. With our vast knowledge and expertise in the Middle East, Asia and Europe destinations, we are able to cater for other countries not mentioned.</p>
      <p>We are constantly expanding our radar to new destinations.</p>
    </div>
  </div>
</section>

<article class="flyer flyer--greece">
  <header class="flyer-head">
    <span class="consultancy"><span class="consultancy-mark"></span>Harrow Lane Advisory</span>
    <span class="series-title">Silver Kite Venture Series</span>
  </header>
  <div class="photo photo--columns" role="img" aria-label="Photograph of classical stone columns against a blue sky">
    <h2 class="destination"><span class="destination-number">Destination 2</span><span class="destination-name">GREECE</span></h2>
  </div>
  <ol class="itinerary">
    <li><span class="day">Day 1</span>Arrival at Athens – Athens city tour</li>
    <li><span class="day">Day 2</span>Athens to Mykonos – Mykonos tour</li>
    <li><span class="day">Day 3</span>Mykonos to Kusadasi – Kusadasi tour</li>
    <li><span class="day">Day 4</span>Kusadasi to Santorini</li>
    <li><span class="day">Day 5</span>Santorini to Athens on cruise – Santorini and volcano, second city tour</li>
    <li><span class="day">Day 6</span>Athens to Delphi by coach – visit hill towns on way – Delphi</li>
    <li><span class="day">Day 7</span>Departure</li>
  </ol>
  <section class="included">
    <h3 class="included-title">What's included in price:</h3>
    <ul>
      <li><svg viewBox="0 0 16 14"><rect x="0" y="3" width="16" height="8" fill="#22313f"/></svg>Air ticket</li>
      <li><svg viewBox="0 0 16 14"><rect x="1" y="6" width="14" height="4" fill="#3f9b35"/><rect x="1" y="3" width="4" height="3" fill="#3f9b35"/></svg>All accommodation</li>
      <li><svg viewBox="0 0 16 14"><circle cx="8" cy="3" r="2.5" fill="#22313f"/><rect x="5" y="6" width="6" height="8" fill="#22313f"/></svg>Full time tour director</li>
      <li><svg viewBox="0 0 16 14"><circle cx="8" cy="7" r="6" fill="#3f9b35"/></svg>Meals</li>
      <li><svg viewBox="0 0 16 14"><rect x="4" y="1" width="1.5" height="13" fill="#22313f"/><rect x="5.5" y="1" width="8" height="5" fill="#3f9b35"/></svg>Tours led by local expert tour guides</li>
      <li><svg viewBox="0 0 16 14"><rect x="1" y="3" width="14" height="8" fill="#3f9b35"/></svg>Entrance fees to attractions</li>
    </ul>
  </section>
</article>

</body>
</html>
```